Cedar Brook Stables, LLC

Equestrian business card to promote equine retirement, farm sitting, short term board. Located in Briar Springs, SC.
Updates
Updated color schemes.
Contact Information for Business Card
Contact info, description of work.
Colors
0094D4
00A9DD
6FCCEA
C7EBF8
E9F6FB
59FF00
82FF00
B8FF75
E3FFCB
F4FFEA
F0912C
F2A743
F7CA91
FBE8D2
FDF5EE

```html
<!DOCTYPE html>
<html lang="en">
<head>
<meta charset="utf-8">
<title>Cedar Brook Stables, LLC – Business Card</title>
<link rel="stylesheet" href="https://fonts.googleapis.com/css2?family=Cinzel:wght@600&family=Libre+Baskerville:wght@400;700&display=swap">
<style>
  :root {
    --backdrop: #2b2b2b;
    --card: #f2ede8;
    --ink: #111111;
    --band: #0a0a0a;
    --accent: #f0912c;
    --coat-dark: #7a4a30;
    --coat-mid: #a8684a;
  }
  * { box-sizing: border-box; margin: 0; padding: 0; }
  html, body { width: 1200px; height: 689px; overflow: hidden; }
  body {
    background: var(--backdrop);
    font-family: "Libre Baskerville", Georgia, serif;
    color: var(--ink);
    position: relative;
  }
  .card {
    position: absolute;
    top: 196px;
    width: 520px;
    height: 297px;
    background: var(--card);
    border-radius: 16px;
    overflow: hidden;
    box-shadow: 0 18px 40px rgba(0,0,0,.45);
  }
  .card--front { left: 45px; }
  .card--back { left: 635px; }

  /* Front */
  .wordmark {
    position: absolute;
    left: 0; right: 0;
    top: 74px;
    font-family: "Cinzel", "Times New Roman", serif;
    font-weight: 600;
    color: var(--ink);
    display: flex;
    flex-direction: column;
    align-items: center;
  }
  .wordmark__name { font-size: 50px; line-height: 1; letter-spacing: 1px; }
  .wordmark__sub-row {
    display: flex;
    align-items: center;
    gap: 10px;
    margin-top: 8px;
    width: 440px;
  }
  .wordmark__rule { flex: 1; height: 1.5px; background: var(--accent); }
  .wordmark__sub { font-size: 20px; letter-spacing: 7px; white-space: nowrap; }
  .services-band {
    position: absolute;
    left: 0; right: 0;
    top: 226px;
    height: 26px;
    background: var(--band);
    color: var(--card);
    font-size: 10.5px;
    letter-spacing: .6px;
    text-transform: uppercase;
    display: flex;
    align-items: center;
    justify-content: center;
    gap: 9px;
  }
  .services-band .dot { width: 4px; height: 4px; background: var(--card); transform: rotate(45deg); }

  /* Back */
  .portrait {
    position: absolute;
    left: 0; bottom: 0;
    width: 300px;
    height: 235px;
    background: radial-gradient(ellipse at 60% 40%, var(--coat-mid), var(--coat-dark) 70%);
    border-top-right-radius: 120px;
  }
  .details {
    position: absolute;
    right: 28px;
    top: 28px;
    text-align: right;
    display: flex;
    flex-direction: column;
    align-items: flex-end;
  }
  .wordmark-small {
    font-family: "Cinzel", "Times New Roman", serif;
    font-weight: 600;
    line-height: 1;
    display: flex;
    flex-direction: column;
    align-items: center;
  }
  .wordmark-small__name { font-size: 26px; }
  .wordmark-small__sub-row {
    display: flex;
    align-items: center;
    gap: 6px;
    margin-top: 4px;
    width: 230px;
  }
  .wordmark-small__sub { font-size: 11px; letter-spacing: 4px; white-space: nowrap; }
  .person { margin-top: 18px; }
  .person__name { font-weight: 700; font-size: 24px; }
  .person__role { color: var(--accent); font-size: 14px; margin-top: 4px; }
  .contact { list-style: none; margin-top: 14px; font-size: 12px; line-height: 1.75; }
  .contact li { display: flex; justify-content: flex-end; align-items: center; gap: 8px; }
  .contact svg { width: 11px; height: 11px; fill: var(--accent); flex: none; }
</style>
</head>
<body>

<section class="card card--front">
  <div class="wordmark">
    <div class="wordmark__name">CEDAR BROOK</div>
    <div class="wordmark__sub-row">
      <span class="wordmark__rule"></span>
      <span class="wordmark__sub">STABLES, LLC</span>
      <span class="wordmark__rule"></span>
    </div>
  </div>
  <div class="services-band">
    <span>Equine Retirement</span><span class="dot"></span>
    <span>Farm Sitting</span><span class="dot"></span>
    <span>Short Term Board</span>
  </div>
</section>

<section class="card card--back">
  <div class="portrait" role="img" aria-label="Photo of a bay horse's head and neck in profile"></div>
  <div class="details">
    <div class="wordmark-small">
      <div class="wordmark-small__name">CEDAR BROOK</div>
      <div class="wordmark-small__sub-row">
        <span class="wordmark__rule"></span>
        <span class="wordmark-small__sub">STABLES, LLC</span>
        <span class="wordmark__rule"></span>
      </div>
    </div>
    <div class="person">
      <div class="person__name">Daniel Hayes</div>
      <div class="person__role">Founder &amp; CEO</div>
    </div>
    <ul class="contact">
      <li>Briar Springs, SC
        <svg viewBox="0 0 12 12"><path d="M6 0a4 4 0 0 0-4 4c0 3 4 8 4 8s4-5 4-8a4 4 0 0 0-4-4zm0 5.6A1.6 1.6 0 1 1 6 2.4a1.6 1.6 0 0 1 0 3.2z"/></svg></li>
      <li>(123) 456-7890
        <svg viewBox="0 0 12 12"><path d="M2.5 0.5l2 2.2-1 1.4a7 7 0 0 0 4.4 4.4l1.4-1 2.2 2-1.2 1.9C5.4 11.2.8 6.6.6 1.7z"/></svg></li>
      <li>info@yourwebsite.com
        <svg viewBox="0 0 12 12"><path d="M0 2h12v8H0zM1 3l5 3.5L11 3z" fill-rule="evenodd"/></svg></li>
      <li>yourwebsite.com
        <svg viewBox="0 0 12 12"><path d="M6 0a6 6 0 1 0 0 12A6 6 0 0 0 6 0zm0 1.2a4.8 4.8 0 1 1 0 9.6 4.8 4.8 0 0 1 0-9.6zM3 5h6v2H3z"/></svg></li>
    </ul>
  </div>
</section>

</body>
</html>
```